Branding product image: VELMOT (Golden Papaya) in Plastic Cup (Ready to Eat)

The product is sliced Fruit in Light syrup
Flavour: VELMOT (Golden Papaya)
The temporary product name: VELMOT
I want the product design to be something 'fun', 'natural', and 'colourful'
The design concept could be anything depends on your imagination, but it must be eye catchy and attractive.
Basically, I want you to be creative in designing the logo and the overall graphic design for the label.
The measurement is 20 cm (Length) x 6,5 cm (Height)
The target customers are young and health conscious audiences (10 years - 65 years old).
Create something different. Something extraordinary.
Brief summary about the fruit:
This fruit only grows in certain part of the world. It grows in mountain area that is in tropical climate. The fruit flesh has a yellowish-golden color. It has an extraordinary taste (unlike normal papaya) and it suits very well with any dishes from cold appetizer, white/ red meat, desserts, and cocktails.
I need a packaging design for Fruit Cup productThe product is sliced Fruit in Light syrup.There will be various flavours i.e. apple, lychee, peach, papaya, etc.However, you may design the product using one sample flavour (i.e. papaya) first, as the designs of other flavours could be adjusted afterwards.The temporary product name is: RICCANAI want the product design to be something 'fun', 'natural', and 'colourful'.The design concept could be anything depends on your imagination. Basically, I want you to be creative in designing the logo and the overall graphic design for the label. - Create something different. Something extraordinary -Additional:The measurement is 20cm (Length) x 5cm (Height).The target customers are young audiences (10 years - 35 years old).The product design must stand out in the supermarket shelf.It must be eye catchy and attractive.Thank you,Jordan-PLEASE REFER TO DESIGN SAMPLE ATTACHED TO HAVE A BETTER UNDERSTANDING FOR THE PRODUCT CONCEPT- Added Wednesday, September 17, 2014
Project Deadline Extended Reason: Haven't found a good design. Added Friday, September 19, 2014
Project Deadline Extended Reason: Need more time for designers to finalize and perfect the design.Thank you,Jordan Added Monday, September 29, 2014
Project Deadline Extended Reason: I haven't found a great design yet. Added Tuesday, February 24, 2015
Reason: Getting better designs now. Still Open to new ideas while refining the latest designs from some designers.
Please do your best in submitting other great designs!

```html
<!DOCTYPE html>
<html lang="en">
<head>
<meta charset="utf-8">
<title>DOSUVEL Golden Papaya Cup Label</title>
<link rel="stylesheet" href="https://fonts.googleapis.com/css2?family=Lato:wght@400;700&family=Kalam:wght@700&display=swap">
<style>
  :root {
    --page: #f1f3f4;
    --green-top: #9bd84c;
    --green-light: #8fd24a;
    --green-deep: #6cc23a;
    --blue-light: #45bdee;
    --blue-mid: #2a9ad8;
    --blue-deep: #1d7fc4;
    --gold: #e9ddb0;
    --white: #ffffff;
    --ink: #1b1b1b;
    --papaya-light: #ffc24d;
    --papaya-mid: #f7a02a;
    --papaya-deep: #e57d14;
  }
  html, body {
    margin: 0;
    padding: 0;
    width: 1200px;
    height: 679px;
    overflow: hidden;
    background: var(--page);
  }
  .canvas {
    position: relative;
    width: 1200px;
    height: 679px;
  }
  .label {
    position: absolute;
    left: 215px;
    top: 140px;
    width: 740px;
    height: 420px;
    overflow: hidden;
  }
  .label__top-band {
    position: absolute;
    left: 0; top: 0;
    width: 100%;
    height: 16px;
    background: linear-gradient(180deg, var(--green-top), var(--green-light));
  }
  .label__main {
    position: absolute;
    left: 0; top: 16px;
    width: 100%;
    height: 307px;
    background:
      radial-gradient(ellipse 55% 70% at 20% 30%, rgba(255,255,255,0.18), rgba(255,255,255,0) 70%),
      radial-gradient(ellipse 45% 60% at 85% 25%, rgba(20,90,160,0.25), rgba(20,90,160,0) 70%),
      linear-gradient(90deg, var(--blue-light), var(--blue-mid) 55%, var(--blue-deep));
  }
  .label__gold-line {
    position: absolute;
    left: 0; top: 323px;
    width: 100%;
    height: 7px;
    background: linear-gradient(90deg, #d9c994, var(--gold) 40%, #fff6d8 60%, #d9c994);
  }
  .label__bottom-band {
    position: absolute;
    left: 0; top: 330px;
    width: 100%;
    height: 90px;
    background: linear-gradient(180deg, var(--green-light), var(--green-deep));
  }
  .brand__dot {
    position: absolute;
    left: 35px;
    top: 58px;
    width: 110px;
    height: 110px;
    border-radius: 50%;
    background: var(--ink);
  }
  .brand__name {
    position: absolute;
    left: 162px;
    top: 58px;
    margin: 0;
    font-family: "Lato", sans-serif;
    font-weight: 700;
    font-size: 112px;
    line-height: 1.2;
    letter-spacing: 1px;
    color: var(--white);
  }
  .flavour {
    position: absolute;
    left: 162px;
    top: 206px;
    margin: 0;
    font-family: "Kalam", cursive;
    font-weight: 700;
    font-size: 34px;
    line-height: 1.25;
    color: var(--white);
  }
  .fruit-visual {
    position: absolute;
    left: 405px;
    top: 222px;
    width: 236px;
    height: 160px;
    border-radius: 50%;
    background: radial-gradient(ellipse at 45% 40%, var(--papaya-light), var(--papaya-mid) 55%, var(--papaya-deep));
  }
  .net-weight {
    position: absolute;
    left: 170px;
    top: 360px;
    margin: 0;
    font-family: "Lato", sans-serif;
    font-size: 22px;
    color: var(--white);
  }
</style>
</head>
<body>
<main class="canvas">
  <section class="label">
    <div class="label__top-band"></div>
    <div class="label__main"></div>
    <div class="label__gold-line"></div>
    <div class="label__bottom-band"></div>

    <span class="brand__dot"></span>
    <h1 class="brand__name">DOSUVEL</h1>

    <p class="flavour">Golden Papaya<br>in Light Syrup</p>

    <div class="fruit-visual" role="img" aria-label="Two halved golden papayas showing orange flesh and dark seeds"></div>

    <p class="net-weight">Net WT 6oz(170g)</p>
  </section>
</main>
</body>
</html>
```